Webdesign für Zahnarztpraxis
Zielgruppe
Zahnarztpraxis
Aufgabenstellung
- Klares und übersichtliches Desgin
- Nicht zu verspielt
- Informativ
- Leichte Naviagtion
- Das Design der alten Webseite soll NICHT kopiert werden
- Die Farben Blau und Grün aus dem Logo sollen sich wiederfinden
- Designbeispiele, die dem Kunden gefallen sind https://www.falkmann-ostrup-zahnarztpraxis.de/ und https://www.zahvilkorn.de/

```html
<!DOCTYPE html>
<html lang="de">
<head>
<meta charset="utf-8">
<title>Praxis Törvald – Dentalpraxis &amp; Labor</title>
<link href="https://fonts.googleapis.com/css2?family=Poppins:wght@400;500;600&display=swap" rel="stylesheet">
<style>
:root{
  --blue-dark:#0b3f86;
  --blue:#0a6fbd;
  --blue-light:#34b8de;
  --green:#5cb132;
  --text:#222a33;
  --page:#f8f9fb;
  --white:#ffffff;
  --alert:#d23a14;
}
*{margin:0;padding:0;box-sizing:border-box}
html,body{width:1003px;height:1200px;overflow:hidden}
body{font-family:"Poppins",sans-serif;background:var(--page);color:var(--text);position:relative}
.abs{position:absolute}
.site-header{left:0;top:0;width:1003px;height:39px;background:var(--white);border-bottom:1px solid #e4e8ee}
.brand{display:flex;align-items:center;gap:6px;font-weight:500;font-size:13px;color:var(--blue);white-space:nowrap}
.brand-dot{width:14px;height:14px;border-radius:50%;background:var(--green)}
.site-header .brand{left:262px;top:11px}
.main-nav{left:396px;top:14px;display:flex;gap:16px;font-size:6px;color:#333;white-space:nowrap}
.main-nav span svg{vertical-align:middle;margin-left:2px}
.hero{left:0;top:39px;width:1003px;height:230px;background:linear-gradient(100deg,var(--blue-dark) 0%,#1a6aa8 55%,var(--blue-light) 100%)}
.hero-kicker{left:265px;top:122px;color:var(--white);font-size:9.8px;font-weight:500;white-space:nowrap}
.hero-title{left:265px;top:139px;color:var(--white);font-size:20px;font-weight:600;line-height:24px;white-space:nowrap}
.portrait{top:79px;width:100px;height:150px;border-radius:8px;background:linear-gradient(180deg,#a9b86a 0%,#d8dfe0 45%,#f1f3f6 100%)}
.service-card{top:249px;width:151px;height:85px;background:var(--white);box-shadow:0 6px 18px rgba(0,0,0,.08);padding:12px 0 0 8px;list-style:none}
.service-card li{font-size:7.2px;font-weight:500;line-height:16.3px;display:flex;align-items:center;gap:4px;white-space:nowrap}
.plus{width:7px;height:7px}
.section-title{color:var(--blue);font-weight:600}
.rooms-title{left:265px;top:381px;font-size:15px;line-height:18px}
.rooms-text{left:265px;top:430px;width:225px;font-size:6.3px;line-height:11.4px}
.room-photo{left:506px;top:382px;width:215px;height:143px;background:linear-gradient(135deg,#5f6d82 0%,#e8e6e0 40%,#d6b07a 75%,#f2f0ea 100%)}
.team-photo{left:318px;top:573px;width:364px;height:152px;background:linear-gradient(180deg,#f0f0f0 0%,#e9e4df 50%,#e8b9b0 100%);box-shadow:0 10px 24px rgba(0,0,0,.08)}
.contact-title{left:265px;top:776px;font-size:15px}
.hours{left:265px;top:806px;font-size:6.3px;line-height:11.4px}
.hours p+p{margin-top:11.4px}
.contact-list{left:514px;top:784px;font-size:8px;font-weight:500;line-height:11px;list-style:none}
.contact-list li{display:flex;gap:8px;align-items:flex-start;margin-bottom:9px;white-space:nowrap}
.contact-list svg{width:12px;height:12px;flex:none}
.house-photo{left:514px;top:860px;width:107px;height:80px;background:linear-gradient(180deg,#3f5a34 0%,#c97a5e 55%,#8a8f88 100%)}
.emergency{left:0;top:1000px;width:1003px;text-align:center;font-size:8.6px;color:var(--blue)}
.emergency-link{left:307px;top:1027px;display:flex;align-items:center;gap:8px;font-size:8.3px;font-weight:500;color:var(--alert);white-space:nowrap}
.site-footer{left:0;top:1094px;width:1003px;height:106px;background:linear-gradient(100deg,var(--blue-dark) 0%,#1a6aa8 55%,var(--blue-light) 100%)}
.site-footer .brand{left:262px;top:48px;color:var(--white)}
.footer-nav{left:391px;top:52px;display:flex;gap:20px;font-size:7px;color:var(--white)}
.footer-rule{left:261px;top:82px;width:478px;height:1px;background:rgba(255,255,255,.8)}
.copyright{left:0;top:91px;width:1003px;text-align:center;font-size:4.8px;color:var(--white)}
</style>
</head>
<body>
<header class="site-header abs">
  <div class="brand abs"><span class="brand-dot"></span>Praxis Törvald</div>
  <nav class="main-nav abs">
    <span>Home</span><span>Unsere Praxis</span>
    <span>Leistungen<svg width="5" height="4" viewBox="0 0 10 6"><path d="M1 1l4 4 4-4" stroke="#0a6fbd" fill="none" stroke-width="1.5"/></svg></span>
    <span>Unser Team</span><span>Anfahrt</span>
  </nav>
</header>

<section class="hero abs"></section>
<div class="hero-kicker abs">Dentalpraxis &amp; Labor Marie Törvald</div>
<h1 class="hero-title abs">Ein starkes Team<br>für Ihre Zähne</h1>
<div class="portrait abs" style="left:463px" role="img" aria-label="Porträtfoto einer Zahnärztin im weißen Praxisoberteil"></div>
<div class="portrait abs" style="left:571px" role="img" aria-label="Porträtfoto einer Mitarbeiterin im weißen Praxisoberteil"></div>
<div class="portrait abs" style="left:679px" role="img" aria-label="Porträtfoto einer Mitarbeiterin im weißen Praxisoberteil"></div>

<ul class="service-card abs" style="left:261px">
  <li><svg class="plus" viewBox="0 0 10 10"><path d="M5 0v10M0 5h10" stroke="#5cb132" stroke-width="2.6"/></svg>Zahnärztliche Diagnostik</li>
  <li><svg class="plus" viewBox="0 0 10 10"><path d="M5 0v10M0 5h10" stroke="#5cb132" stroke-width="2.6"/></svg>Individualprophylaxe</li>
  <li><svg class="plus" viewBox="0 0 10 10"><path d="M5 0v10M0 5h10" stroke="#5cb132" stroke-width="2.6"/></svg>Professionelle Zahnreinigung</li>
  <li><svg class="plus" viewBox="0 0 10 10"><path d="M5 0v10M0 5h10" stroke="#5cb132" stroke-width="2.6"/></svg>Bioverträglicher Zahnersatz</li>
</ul>
<ul class="service-card abs" style="left:425px">
  <li><svg class="plus" viewBox="0 0 10 10"><path d="M5 0v10M0 5h10" stroke="#5cb132" stroke-width="2.6"/></svg>Konservierende Zahnheilkunde</li>
  <li><svg class="plus" viewBox="0 0 10 10"><path d="M5 0v10M0 5h10" stroke="#5cb132" stroke-width="2.6"/></svg>Zahnärztliche Prothetik</li>
  <li><svg class="plus" viewBox="0 0 10 10"><path d="M5 0v10M0 5h10" stroke="#5cb132" stroke-width="2.6"/></svg>Kieferorthopädie</li>
  <li><svg class="plus" viewBox="0 0 10 10"><path d="M5 0v10M0 5h10" stroke="#5cb132" stroke-width="2.6"/></svg>Eigenes Praxislabor</li>
</ul>
<ul class="service-card abs" style="left:588px">
  <li><svg class="plus" viewBox="0 0 10 10"><path d="M5 0v10M0 5h10" stroke="#5cb132" stroke-width="2.6"/></svg>Chirurgische Zahnheilkunde</li>
  <li><svg class="plus" viewBox="0 0 10 10"><path d="M5 0v10M0 5h10" stroke="#5cb132" stroke-width="2.6"/></svg>Ästhetische Zahnheilkunde</li>
  <li><svg class="plus" viewBox="0 0 10 10"><path d="M5 0v10M0 5h10" stroke="#5cb132" stroke-width="2.6"/></svg>Ganzheitliche Zahnheilkunde</li>
  <li><svg class="plus" viewBox="0 0 10 10"><path d="M5 0v10M0 5h10" stroke="#5cb132" stroke-width="2.6"/></svg>Kinderzahnheilkunde</li>
</ul>

<h2 class="section-title rooms-title abs">Moderne Praxisräume, in<br>denen Lächeln leichtfällt</h2>
<p class="rooms-text abs">Helle Farben, natürliche Materialien und viel Platz schaffen eine ruhige Atmosphäre, in der Sie sich sofort wohlfühlen. Unser Zahnarzt ist freundlich, nahbar und sympathisch – nimmt sich Zeit, erklärt jeden Schritt verständlich und behandelt mit ruhiger Hand, auch bei Angstpatient:innen. Mit moderner Technik, höchsten Hygienestandards und kurzen Wegen sorgen wir dafür, dass Ihr Besuch entspannt, transparent und angenehm verläuft.</p>
<div class="room-photo abs" role="img" aria-label="Heller Behandlungsraum mit Zahnarztstuhl und Holzmöbeln"></div>

<div class="team-photo abs" role="img" aria-label="Gruppenfoto des fünfköpfigen Praxisteams"></div>

<h2 class="section-title contact-title abs">Wir sind für Sie da.</h2>
<div class="hours abs">
  <p>ÖFFNUNGSZEITEN<br>Montag: 09:00–13:00 und 14:00–19:00<br>Dienstag: 09:00–13:00 und 14:00–19:00<br>Mittwoch: 09:00–14:00<br>Donnerstag: geschlossen<br>Freitag: 09:00–13:00<br>… und nach Vereinbarung</p>
  <p>TELEFONISCHE ERREICHBARKEIT<br>Innerhalb dieser Zeiten sind wir telefonisch für Sie da:<br>Montag: 09:00–15:00<br>Dienstag: 09:00–15:00<br>Mittwoch: 09:00–12:00</p>
</div>
<ul class="contact-list abs">
  <li><svg viewBox="0 0 24 24"><path d="M6.6 10.8a15 15 0 006.6 6.6l2.2-2.2a1 1 0 011-.25 11.4 11.4 0 003.6.57 1 1 0 011 1V20a1 1 0 01-1 1A17 17 0 013 4a1 1 0 011-1h3.5a1 1 0 011 1c0 1.25.2 2.45.57 3.57a1 1 0 01-.25 1z" fill="#5cb132"/></svg>01234-48170</li>
  <li><svg viewBox="0 0 24 24"><rect x="2" y="4" width="20" height="16" fill="none" stroke="#5cb132" stroke-width="2"/><path d="M2 4l10 9 10-9M2 20l8-8M22 20l-8-8" fill="none" stroke="#5cb132" stroke-width="2"/></svg>info@zahnarztpraxis-toervald.de</li>
  <li><svg viewBox="0 0 24 24"><path d="M12 2a7 7 0 00-7 7c0 5 7 13 7 13s7-8 7-13a7 7 0 00-7-7z" fill="#5cb132"/><circle cx="12" cy="9" r="2.5" fill="#fff"/></svg><span>Lindenstraße 14<br>01234 Wiesenau</span></li>
</ul>
<div class="house-photo abs" role="img" aria-label="Außenansicht des Praxisgebäudes"></div>

<p class="emergency abs">In dringenden Fällen wenden Sie sich bitte an zahnärtlichen Notdienst.</p>
<div class="emergency-link abs">
  <svg width="16" height="13" viewBox="0 0 32 26"><path d="M2 4h18v16H2z M20 9h6l4 5v6H20z" fill="#d23a14"/><circle cx="8" cy="21" r="3" fill="#d23a14" stroke="#f8f9fb" stroke-width="1.5"/><circle cx="25" cy="21" r="3" fill="#d23a14" stroke="#f8f9fb" stroke-width="1.5"/><path d="M11 7v9M6.5 11.5h9" stroke="#fff" stroke-width="2.4"/></svg>
  Link 'zur Notdienstsuche' https://www.zahnnotdienst-region.de/patienten/notdienstsuche/
</div>

<footer class="site-footer abs">
  <div class="brand abs"><span class="brand-dot"></span>Praxis Törvald</div>
  <nav class="footer-nav abs"><span>Impressum</span><span>Datenschutz</span></nav>
  <div class="footer-rule abs"></div>
  <p class="copyright abs">© Copyright 2018 - 2025 Nordlicht Webdesign GmbH | proudly crafted by Tobias Wendler</p>
</footer>
</body>
</html>
```